Brevlon Website Design - Wordpress

Need a website WordPress design for our existing website that we just stood up. The logo is already in place and name. Brevlon.example We are a company which makes connections with our clients through educating them and providing networking events. We would like for the website to show a VIP/special feel to it.

Target Market(s)

Business executives and employees. Age group 26-65 in the following sectors:
- Technology
- Human Resources
- Finance
- Sales

Industry/Entity Type

Technical Service

Number of Pages Required

4 page

Font styles to use
Sans Serif

Requirements
Must have
• Must be something for Wordpress
Nice to have
• Would like this to be professional but look cutting edge and VIP.

```html
<!DOCTYPE html>
<html lang="en">
<head>
<meta charset="utf-8">
<title>Brevlon — Expand Your Business</title>
<link href="https://fonts.googleapis.com/css2?family=Lato:wght@400;700;900&display=swap" rel="stylesheet">
<style>
:root{
  --ink:#ffffff;
  --muted:#d8d8d8;
  --bg-dark:#1e1e1e;
  --bg-black:#050505;
  --bg-team:#191919;
  --gold:#e8b01e;
  --red:#c8202f;
  --purple:#6e2c8c;
  --blue:#1f5f9e;
  --green:#1f9a3e;
  --mind:#2a6fa8;
}
*{margin:0;padding:0;box-sizing:border-box}
html,body{width:1200px;height:4045px;overflow:hidden}
body{font-family:'Lato',sans-serif;color:var(--ink);background:var(--bg-dark);position:relative}
.abs{position:absolute}
.dots{background-image:radial-gradient(rgba(255,255,255,.05) 1px,transparent 1.5px);background-size:6px 6px}

/* header & hero */
.hero{left:0;top:0;width:1200px;height:760px;background:radial-gradient(ellipse at 55% 35%,#3a3550 0%,#16162a 45%,#05060c 100%)}
.brand{left:110px;top:58px;display:flex;align-items:center;gap:16px;font-size:40px;font-weight:700;letter-spacing:4px}
.brand-mark{width:40px;height:40px;background:var(--gold)}
.nav{right:108px;top:68px;display:flex;gap:44px;font-size:18px;font-weight:700;letter-spacing:1.5px}
.hero-title{left:0;width:1200px;top:295px;text-align:center;font-size:56px;font-weight:700;letter-spacing:5px}
.hero-btn{left:507px;top:442px;width:186px;height:54px;border:3px solid var(--gold);color:var(--gold);font-size:17px;font-weight:700;letter-spacing:1.5px;display:flex;align-items:center;justify-content:center}
.hero-arrow{top:345px}

/* strategy */
.strategy{left:0;top:640px;width:1200px;height:965px;background:var(--bg-dark)}
.section-title{left:0;width:1200px;text-align:center;font-size:34px;font-weight:700;letter-spacing:2.5px}
.lede{left:0;width:1200px;text-align:center;font-size:22px;line-height:48px;letter-spacing:1px}
.pillar{font-size:26px;line-height:44px;letter-spacing:1.5px}
.pillar .tag{display:block;font-weight:400}
.pillar .word{display:block;font-weight:700}
.pillar.left{text-align:right;width:300px}
.strategy-core{left:470px;top:1100px;width:270px;height:300px;background:linear-gradient(135deg,var(--blue),var(--purple) 50%,var(--gold))}

/* offer */
.offer{left:0;top:1605px;width:1200px;height:660px;background:var(--bg-black)}
.offer-card{top:1861px;width:216px;height:167px;border:3px solid #fff;font-size:14px;line-height:17px;text-align:center;padding:28px 14px 0}
.offer-icon{top:1826px;width:70px;height:70px;border-radius:50%;background:#fff;border:3px solid #000;display:flex;align-items:center;justify-content:center}
.value-btn{left:485px;top:2130px;width:189px;height:68px;border-radius:6px;background:var(--gold);box-shadow:0 0 30px rgba(232,176,30,.55);font-size:22px;font-weight:700;display:flex;align-items:center;justify-content:center}

/* unique */
.unique{left:0;top:2265px;width:1200px;height:620px;background:#1b1b1b}
.unique-title{left:0;width:1200px;top:2470px;text-align:center;font-size:54px;font-weight:700;letter-spacing:4px;color:var(--red)}
.values{left:0;width:1200px;top:2572px;text-align:center;font-size:32px;font-weight:700;letter-spacing:1.5px}
.unique-text{left:250px;width:700px;top:2640px;text-align:center;font-size:20px;line-height:31px;font-weight:700;letter-spacing:.5px}

/* team */
.team{left:0;top:2880px;width:1200px;height:740px;background:var(--bg-team)}
.portrait-frame{width:232px;height:235px;border:5px solid var(--green);transform:rotate(-3deg)}
.portrait{width:232px;height:235px;background:linear-gradient(160deg,#9a9a9a,#3e3e3e)}
.bio{width:420px;text-align:center;font-size:19px;line-height:32px;letter-spacing:.5px}
.more{width:34px;height:34px;border-radius:50%;border:2px solid var(--green)}

/* footer */
.footer{left:0;top:3614px;width:1200px;height:391px;background:var(--bg-dark)}
.foot-head{font-size:28px;font-weight:900;letter-spacing:1.5px}
.foot-line{font-size:17px;letter-spacing:1px;display:flex;align-items:center;gap:8px}
.event-banner{left:440px;top:3768px;width:280px;height:121px;background:linear-gradient(110deg,var(--red),var(--purple) 55%,var(--gold))}
.search{left:828px;top:3784px;width:272px;height:41px;border:2px solid var(--green);border-radius:8px;font-size:15px;font-style:italic;color:#aaa;padding:10px 20px}
.social{top:3859px;width:34px;height:34px;border-radius:50%;background:#fff}
.foot-nav{left:0;width:1200px;top:3936px;text-align:center;font-size:16px;letter-spacing:1px}
.copyright{left:0;top:4005px;width:1200px;height:40px;background:#000;font-size:15px;display:flex;align-items:center;justify-content:center}
</style>
</head>
<body>

<!-- header & hero -->
<div class="abs hero" role="img" aria-label="Night sky full of stars with a person standing on a hilltop"></div>
<svg class="abs" style="left:0;top:620px" width="1200" height="150" viewBox="0 620 1200 150">
  <polygon points="0,634 810,755 1200,647 1200,770 0,770" fill="var(--bg-dark)"/>
  <polyline points="0,634 810,755 1200,647" fill="none" stroke="var(--gold)" stroke-width="8"/>
</svg>
<div class="abs brand"><span class="brand-mark"></span>BREVLON</div>
<nav class="abs nav"><span>EVENTS</span><span>EXPAND</span><span>X</span><span>ABOUT</span><span>CONNECT</span></nav>
<h1 class="abs hero-title">EXPAND YOUR BUSINESS</h1>
<svg class="abs hero-arrow" style="left:68px" width="30" height="56"><polyline points="26,4 4,28 26,52" fill="none" stroke="#fff" stroke-width="3"/></svg>
<svg class="abs hero-arrow" style="left:1102px" width="30" height="56"><polyline points="4,4 26,28 4,52" fill="none" stroke="#fff" stroke-width="3"/></svg>
<div class="abs hero-btn">LEARN MORE</div>

<!-- strategy -->
<section class="abs strategy dots"></section>
<svg class="abs" style="left:0;top:620px" width="1200" height="150" viewBox="0 620 1200 150">
  <polyline points="0,634 810,755 1200,647" fill="none" stroke="var(--gold)" stroke-width="8"/>
</svg>
<h2 class="abs section-title" style="top:845px">IT'S ABOUT OUR UNIQUE X STRATEGY</h2>
<p class="abs lede" style="top:922px">BREVLON provides impactful connection opportunities to help educate,<br>equip and expand you and your business</p>

<div class="abs pillar left" style="left:15px;top:1140px"><span class="tag" style="color:var(--mind)">MIND</span><span class="word">THOUGHT</span></div>
<svg class="abs" style="left:336px;top:1160px" width="50" height="50"><circle cx="25" cy="25" r="22" fill="var(--mind)"/></svg>
<div class="abs pillar left" style="left:15px;top:1276px"><span class="tag" style="color:var(--purple)">SOUL</span><span class="word">INTUITION</span></div>
<svg class="abs" style="left:336px;top:1296px" width="50" height="50"><circle cx="25" cy="25" r="22" fill="var(--purple)"/></svg>

<svg class="abs" style="left:784px;top:1162px" width="52" height="46" viewBox="0 0 52 46"><path d="M26 44 L4 22 A12 12 0 0 1 26 8 A12 12 0 0 1 48 22 Z" fill="var(--red)"/></svg>
<div class="abs pillar" style="left:863px;top:1140px"><span class="tag" style="color:var(--red)">HEART</span><span class="word">EMOTIONS</span></div>
<svg class="abs" style="left:784px;top:1296px" width="50" height="50"><circle cx="25" cy="25" r="22" fill="var(--gold)"/></svg>
<div class="abs pillar" style="left:863px;top:1276px"><span class="tag" style="color:var(--gold)">STRENGTH</span><span class="word">ENERGY</span></div>
<div class="abs strategy-core" role="img" aria-label="Strategy emblem area"></div>

<!-- offer -->
<section class="abs offer"></section>
<h2 class="abs section-title" style="top:1688px">WHAT WE OFFER YOU</h2>

<div class="abs offer-icon" style="left:175px"><svg width="30" height="36"><path d="M15 34 C4 20 3 14 3 12 A12 12 0 0 1 27 12 C27 14 26 20 15 34Z" fill="var(--red)"/><circle cx="15" cy="12" r="5" fill="#fff"/></svg></div>
<div class="abs offer-card" style="left:102px">At BREVLON, we provide effective training and learning as the foundation for building a healthy, successful company.</div>
<div class="abs offer-icon" style="left:434px"><svg width="34" height="34"><rect x="4" y="4" width="26" height="26" rx="4" fill="var(--mind)"/></svg></div>
<div class="abs offer-card" style="left:361px">Through our connected ecosystem of companies, we'll help find the right partners for equipping you to move forward.</div>
<div class="abs offer-icon" style="left:693px"><svg width="40" height="30"><circle cx="11" cy="15" r="9" fill="var(--gold)"/><circle cx="29" cy="15" r="9" fill="var(--gold)"/></svg></div>
<div class="abs offer-card" style="left:620px">We connect you with others who have successfully implemented our X Strategy to facilitate growth in their business.</div>
<div class="abs offer-icon" style="left:952px"><svg width="30" height="38"><rect x="7" y="2" width="16" height="34" fill="var(--mind)"/></svg></div>
<div class="abs offer-card" style="left:879px">Our goal is to help you and your business increase productivity and scale through effective strategy and healthy culture.</div>

<div class="abs value-btn">X= Value</div>

<!-- unique -->
<section class="abs unique dots"></section>
<svg class="abs" style="left:0;top:2255px" width="1200" height="150" viewBox="0 2255 1200 150">
  <polygon points="0,2265 513,2265 1011,2387 1200,2279 1200,2255 0,2255" fill="var(--bg-black)"/>
  <polyline points="513,2265 1011,2387 1200,2279" fill="none" stroke="var(--purple)" stroke-width="9"/>
</svg>
<h2 class="abs unique-title">X = UNIQUE</h2>
<p class="abs values"><span style="color:var(--gold)">Virtue</span> | <span style="color:var(--purple)">Appreciation</span> | <span style="color:var(--blue)">Respect</span> | <span style="color:var(--green)">Ownership</span></p>
<p class="abs unique-text">Our team is an unusual mix. We're globally experienced, technically capable, community focussed and highly fruitful. The four core values above inform everything we do. Our special sauce is knowing how to fuse structure and productivity with relationship and creativity.</p>

<!-- team -->
<section class="abs team"></section>
<svg class="abs" style="left:0;top:2850px" width="1200" height="140" viewBox="0 2850 1200 140">
  <polygon points="0,2850 1200,2850 1200,2872 162,2980 0,2859" fill="#1b1b1b"/>
  <polyline points="0,2859 162,2980 1200,2872" fill="none" stroke="var(--gold)" stroke-width="9"/>
</svg>

<div class="abs portrait-frame" style="left:256px;top:3080px"></div>
<div class="abs portrait" style="left:248px;top:3088px" role="img" aria-label="Black and white portrait of team member Marcus Hale"></div>
<p class="abs bio" style="left:158px;top:3361px">Marcus Hale has lived and worked in several countries, experiencing varied cultures and companies.</p>
<svg class="abs more" style="left:347px;top:3474px;border:none" width="36" height="36"><circle cx="18" cy="18" r="15" fill="none" stroke="var(--green)" stroke-width="2"/><polyline points="11,18 25,18 20,13 M25,18 20,23" fill="none" stroke="var(--green)" stroke-width="2"/><path d="M20 13 L25 18 L20 23" fill="none" stroke="var(--green)" stroke-width="2"/></svg>

<div class="abs portrait-frame" style="left:758px;top:3080px"></div>
<div class="abs portrait" style="left:750px;top:3088px" role="img" aria-label="Black and white portrait of team member Daniel Ortiz"></div>
<p class="abs bio" style="left:658px;top:3361px">Daniel Ortiz is highly experienced as an entrepreneur, business owner and marketing expert.</p>
<svg class="abs" style="left:862px;top:3474px" width="36" height="36"><circle cx="18" cy="18" r="15" fill="none" stroke="var(--green)" stroke-width="2"/><line x1="11" y1="18" x2="25" y2="18" stroke="var(--green)" stroke-width="2"/><path d="M20 13 L25 18 L20 23" fill="none" stroke="var(--green)" stroke-width="2"/></svg>

<!-- footer -->
<footer class="abs footer dots"></footer>
<svg class="abs" style="left:0;top:3480px" width="1200" height="160" viewBox="0 3480 1200 160">
  <polygon points="0,3506 890,3628 1200,3490 1200,3640 0,3640" fill="var(--bg-dark)"/>
  <polyline points="0,3506 890,3628 1200,3490" fill="none" stroke="var(--blue)" stroke-width="9"/>
</svg>

<h3 class="abs foot-head" style="left:135px;top:3724px">CONTACT US</h3>
<div class="abs foot-line" style="left:135px;top:3775px"><svg width="14" height="16"><path d="M3 1 L6 1 L7 5 L5 7 C6 10 7 11 10 12 L12 10 L15 11 L15 14 C8 15 1 8 3 1Z" fill="var(--red)"/></svg>1-855-555-0142</div>
<div class="abs foot-line" style="left:135px;top:3815px"><svg width="16" height="12"><rect x="0" y="0" width="16" height="12" fill="var(--red)"/><polyline points="0,0 8,7 16,0" fill="none" stroke="#1e1e1e" stroke-width="1.5"/></svg>CONNECT@BREVLON.EXAMPLE</div>

<h3 class="abs foot-head" style="left:445px;top:3722px">MEET UP</h3>
<div class="abs event-banner" role="img" aria-label="Promotional banner for the Expand Your Business event"></div>

<h3 class="abs foot-head" style="left:823px;top:3722px">SEARCH</h3>
<div class="abs search">Search</div>
<svg class="abs" style="left:1062px;top:3794px" width="22" height="22"><circle cx="9" cy="9" r="6.5" fill="none" stroke="var(--green)" stroke-width="2.5"/><line x1="14" y1="14" x2="20" y2="20" stroke="var(--green)" stroke-width="2.5"/></svg>
<div class="abs social" style="left:881px"></div>
<div class="abs social" style="left:930px"></div>
<div class="abs social" style="left:981px"></div>

<nav class="abs foot-nav">EVENTS &nbsp;| &nbsp;EXPAND &nbsp;| &nbsp;X &nbsp;| &nbsp;ABOUT &nbsp;| &nbsp;CONNECT</nav>
<div class="abs copyright">Copyrights 2019. All rights reserved</div>

</body>
</html>
```